SnackOrbit!!! A Vending Machine Business Looking for an attractive website.

We are a vending machine business in Northern Michigan. We have changed our name and have rebranded our company. We would like an attractive website that shares who we are, what services we provide, the products we offer in our machines, along with a form businesses can fill out to see if they are a good fit for our company. I would like to have a Home Page, About SnackOrbit, Why Choose SnackOrbit?, Products & Services, Contact Us (With a Login Option), and a page with a questionnaire for thos interested in getting a FREE Vending Machine.

Target Market(s)

Businesses, Campgrounds, Schools, and many more in Northern Michigan

Industry/Entity Type

Vending Machines

Coding

Coded - Design and coding required

Number of Pages Required

5+ page

Requirements
Must have
• An inviting and enticing Home Page. I want to get my potential clients engaged in our website.
Nice to have
• Possibly background photos from Northern Michigan
Should not have
• A corporate feel. I do not want a boring website.

```html
<!DOCTYPE html>
<html lang="en">
<head>
<meta charset="utf-8">
<title>SnackOrbit – Crave. Vend. Repeat.</title>
<link href="https://fonts.googleapis.com/css2?family=Poppins:wght@400;500;600;700;800&family=Gelasio:wght@700&display=swap" rel="stylesheet">
<style>
:root{
  --navy:#27235f;
  --navy-dark:#1f1c4f;
  --green:#2b4d22;
  --green-bright:#2f5a25;
  --ink:#111;
  --text:#333;
  --muted:#f3f3f5;
  --white:#fff;
}
*{box-sizing:border-box;margin:0;padding:0}
html,body{width:1200px;height:3924px;overflow:hidden}
body{position:relative;font-family:"Poppins",sans-serif;color:var(--text);background:var(--white)}
.serif{font-family:"Gelasio",serif;font-weight:700}
.btn{position:absolute;display:flex;align-items:center;justify-content:center;gap:6px;font-weight:500;font-size:13px;border-radius:6px;color:var(--white)}
.btn-green{background:var(--green)}
.btn-navy{background:var(--navy)}
.t-green{color:var(--green)}
.t-navy{color:var(--navy)}

/* header */
.site-header{position:absolute;left:0;top:0;width:1200px;height:84px;background:var(--white)}
.brand{position:absolute;left:107px;top:20px;display:flex;align-items:center;gap:10px;font-weight:800;font-size:30px;color:var(--navy)}
.brand-dot{width:26px;height:26px;border-radius:50%;background:var(--green)}
.nav{position:absolute;left:393px;top:32px;display:flex;gap:33px;font-size:13.5px;color:#222}
.pill{border-radius:20px;font-size:14px}

/* hero */
.hero{position:absolute;left:0;top:84px;width:1200px;height:543px;background:linear-gradient(100deg,#140d08 0%,#2a1c12 35%,#4a3a26 62%,#6b6140 80%,#332a20 100%)}
.hero h1{position:absolute;left:107px;top:168px;font-size:41px;line-height:48px;font-weight:800;color:var(--white)}
.hero p{position:absolute;left:106px;top:279px;font-size:17px;color:var(--white);letter-spacing:.3px}
.hero .btn{left:106px;top:327px;width:141px;height:43px;border-radius:22px;font-size:14px}

/* about */
.about{position:absolute;left:0;top:627px;width:1200px;height:514px;background:linear-gradient(180deg,#fff 70%,#eef1f6 100%)}
.about-arc{position:absolute;left:140px;top:85px}
.about-photo{position:absolute;left:158px;top:90px;width:396px;height:396px;border-radius:50%;background:radial-gradient(circle at 70% 40%,#c6d6e6 0%,#b02638 35%,#6d3a7c 60%,#2a1d2a 100%)}
.about h2{position:absolute;left:621px;top:84px;font-size:43px;font-weight:800;color:var(--ink)}
.about .rule{position:absolute;left:621px;top:148px;width:48px;height:2px;background:var(--ink)}
.about .copy{position:absolute;left:621px;top:166px;width:437px;font-size:12.2px;line-height:21.5px;text-align:justify;color:#222}
.about .copy p{margin-bottom:11px}
.about .btn-outline{position:absolute;left:621px;top:438px;width:133px;height:39px;border:1.5px solid var(--green);border-radius:20px;color:var(--green);font-size:13px;display:flex;align-items:center;justify-content:center;gap:6px;font-weight:500}

/* machines */
.machines{position:absolute;left:0;top:1141px;width:1200px;height:755px}
.machine-panel{position:absolute;top:0;height:755px;width:600px;text-align:center;color:var(--white)}
.machine-panel.navy{left:0;background:linear-gradient(180deg,#2c2868,#262260)}
.machine-panel.green{left:598px;width:602px;background:linear-gradient(160deg,#2f5a25,#2a4f22)}
.machine-photo{position:absolute;border-radius:4px}
.machine-panel h3{position:absolute;left:0;width:100%;top:518px;font-size:27px}
.machine-panel p{position:absolute;left:90px;width:420px;top:558px;font-size:12px;line-height:23px}
.machine-panel .btn{top:644px;width:123px;height:33px;font-size:12px;font-weight:600}

/* why */
.why{position:absolute;left:0;top:1896px;width:1200px;height:716px}
.section-title{position:absolute;left:0;width:100%;text-align:center;font-size:40px;color:var(--ink)}
.why .section-title{top:78px}
.tab{position:absolute;top:172px;width:173px;height:125px;background:var(--white);box-shadow:0 2px 8px rgba(0,0,0,.08);display:flex;flex-direction:column;align-items:center;justify-content:center;gap:10px;font-size:12.5px;font-weight:500;text-align:center;line-height:15px;color:#222}
.tab.active{background:var(--green);color:var(--white);box-shadow:none}
.tab.active::after{content:"";position:absolute;bottom:-10px;left:77px;border:10px solid transparent;border-bottom:0;border-top-color:var(--green)}
.why h4{position:absolute;left:145px;top:385px;font-size:34px;color:var(--ink)}
.why .copy{position:absolute;left:145px;top:437px;width:420px;font-size:14.5px;line-height:31px;color:#222}
.why-photo{position:absolute;left:635px;top:355px;width:420px;height:265px;border-radius:6px;background:linear-gradient(90deg,#07080b 0%,#101217 35%,#3e4e6a 60%,#8fa7c4 78%,#d9c7ad 100%)}

/* testimonials */
.reviews{position:absolute;left:0;top:2612px;width:1200px;height:499px;background:var(--muted)}
.reviews .section-title{top:90px}
.review{position:absolute;top:180px;width:444px;height:224px;background:var(--white);border-radius:6px;box-shadow:0 2px 10px rgba(0,0,0,.08);text-align:center;padding:105px 20px 0}
.review::after{content:"";position:absolute;left:12px;right:12px;bottom:0;height:3px;background:var(--navy)}
.quote{position:absolute;left:182px;top:30px;font-size:110px;line-height:110px;color:#e4e4ea;font-family:"Gelasio",serif}
.stars{position:absolute;left:0;width:100%;top:73px;color:#f2b51c;font-size:17px;letter-spacing:2px}
.review p{position:relative;font-size:10.5px;line-height:19px;color:#222}
.review h5{position:relative;margin-top:10px;font-size:15px;line-height:20px;color:var(--ink)}
.arrow{position:absolute;top:255px;width:37px;height:37px;border-radius:50%;display:flex;align-items:center;justify-content:center}
.arrow.prev{left:84px;border:1.5px solid #cfcfcf;background:var(--white)}
.arrow.next{left:1080px;background:var(--green)}

/* cta */
.cta{position:absolute;left:0;top:3111px;width:1200px;height:392px;text-align:center}
.cta h2{position:absolute;left:0;width:100%;top:96px;font-size:40px;line-height:51px;color:var(--ink)}
.cta p{position:absolute;left:0;width:100%;top:200px;font-size:14px;line-height:27px;font-weight:500;color:#222}
.cta .btn{left:544px;top:265px;width:112px;height:38px;font-size:12px;font-weight:600}

/* footer */
.footer{position:absolute;left:0;top:3503px;width:1200px;height:365px}
.footer svg.wave{position:absolute;left:0;top:0}
.foot-col h6{font-family:"Gelasio",serif;font-size:19px;color:var(--white);margin-bottom:16px}
.links{position:absolute;left:145px;top:130px}
.links li{list-style:none;color:var(--white);font-size:12px;line-height:30px;display:flex;align-items:center;gap:8px}
.links li::before{content:"";border:4px solid transparent;border-right:0;border-left:5px solid var(--white)}
.foot-brand{position:absolute;left:420px;top:158px;width:360px;display:flex;justify-content:center;align-items:center;gap:12px;font-weight:800;font-size:54px;color:var(--white)}
.foot-brand .brand-dot{width:40px;height:40px;background:var(--green-bright)}
.socials{position:absolute;left:517px;top:272px;display:flex;gap:7px}
.socials span{width:28px;height:28px;border:1.5px solid var(--white);border-radius:50%}
.contact{position:absolute;left:868px;top:130px}
.contact-row{display:flex;gap:12px;color:var(--white);font-size:12px;line-height:19px;margin-bottom:14px}
.contact-row svg{flex:none;margin-top:4px}
.copyright{position:absolute;left:0;top:3868px;width:1200px;height:56px;background:var(--green);color:var(--white);display:flex;align-items:center;justify-content:center;font-family:"Gelasio",serif;font-size:13px}
</style>
</head>
<body>

<header class="site-header">
  <div class="brand"><span class="brand-dot"></span>SnackOrbit</div>
  <nav class="nav">
    <span>Home</span><span>About SnackOrbit</span><span>Why Choose Us?</span><span>Products &amp; Services</span>
  </nav>
  <span class="btn btn-green pill" style="left:912px;top:24px;width:99px;height:36px">Contact Us</span>
  <span class="btn btn-navy pill" style="left:1023px;top:24px;width:71px;height:36px">Login</span>
</header>

<section class="hero" role="img" aria-label="Brightly lit vending machines stocked with drinks in a dark setting">
  <h1>SnackOrbit: Crave.<br>Vend. Repeat.</h1>
  <p>Elevating Snacking, One Vend at a Time</p>
  <span class="btn btn-green">Contact Us
    <svg width="12" height="12" viewBox="0 0 12 12"><path d="M1 6h9M6 2l4 4-4 4" stroke="#fff" stroke-width="2" fill="none"/></svg></span>
</section>

<section class="about">
  <svg class="about-arc" width="420" height="420" viewBox="0 0 420 420">
    <path d="M214 8 A202 202 0 1 0 214 412" stroke="#2b4d22" stroke-width="10" fill="none"/>
  </svg>
  <div class="about-photo" role="img" aria-label="Woman in a floral robe choosing from a lit vending machine"></div>
  <h2>About <span class="t-green">Snack</span><span class="t-navy">Orbit</span></h2>
  <div class="rule"></div>
  <div class="copy">
    <p>Welcome to <b>SnackOrbit,</b> where snacking meets delight! We’re not just about vending machines; we’re your culinary companions, your flavor curators, and your secret stash of happiness. Mark and Elena, the dynamic duo behind SnackOrbit, have a passion for all things tasty. With backgrounds in sales and a penchant for personal connections, they’ve transformed the vending experience into an art form.</p>
    <p>At <b>SnackOrbit,</b> we don’t just vend snacks—we curate cravings. Our customized vending solutions bring flavor, convenience, and community to Northern Michigan. Whether you’re reaching for a <b>mid-morning snack</b>, a <b>refreshing beverage</b>, or a <b>satisfying breakfast burrito,</b> SnackOrbit delivers delight with every bite.</p>
  </div>
  <span class="btn-outline">Read More
    <svg width="12" height="12" viewBox="0 0 12 12"><path d="M1 6h9M6 2l4 4-4 4" stroke="#2b4d22" stroke-width="2" fill="none"/></svg></span>
</section>

<section class="machines">
  <div class="machine-panel navy">
    <div class="machine-photo" role="img" aria-label="Snack vending machine filled with chips and candy" style="left:251px;top:92px;width:244px;height:412px;background:linear-gradient(180deg,#2c2c30,#4b4f58 50%,#1c1c20)"></div>
    <h3 class="serif">Vending Machine - 1</h3>
    <p>Lorem ipsum dolor sit amet, consectetuer adipiscing elit, sed diam nonummy nibh euismod tincidunt ut laoreet dolore magna aliquam erat volutpat. Ut wisi enim ad minim veniam.</p>
    <span class="btn btn-green" style="left:310px">View Details</span>
  </div>
  <div class="machine-panel green">
    <div class="machine-photo" role="img" aria-label="Combo vending machine with snacks and bottled drinks" style="left:125px;top:90px;width:212px;height:417px;background:linear-gradient(180deg,#1a1d26,#3a4866 50%,#141620)"></div>
    <h3 class="serif">Vending Machine - 2</h3>
    <p>Lorem ipsum dolor sit amet, consectetuer adipiscing elit, sed diam nonummy nibh euismod tincidunt ut laoreet dolore magna aliquam erat volutpat. Ut wisi enim ad minim veniam.</p>
    <span class="btn btn-navy" style="left:170px">View Details</span>
  </div>
</section>

<section class="why">
  <h2 class="section-title serif">Why Choose <span class="t-green">Snack</span><span class="t-navy">Orbit</span></h2>
  <div class="tab active" style="left:203px">
    <svg width="36" height="42" viewBox="0 0 36 42"><path d="M18 40C8 30 3 23 3 16a15 15 0 0 1 30 0c0 7-5 14-15 24z" stroke="#fff" stroke-width="2" fill="none"/><path d="M18 25l-6-6a3.5 3.5 0 0 1 6-4 3.5 3.5 0 0 1 6 4z" stroke="#fff" stroke-width="2" fill="none"/></svg>
    Local Love</div>
  <div class="tab" style="left:410px">
    <svg width="46" height="42" viewBox="0 0 46 42"><circle cx="17" cy="17" r="14" stroke="#2b4d22" stroke-width="2" fill="none"/><circle cx="31" cy="26" r="12" stroke="#27235f" stroke-width="2" fill="none"/></svg>
    Unleash Your<br>Cravings</div>
  <div class="tab" style="left:615px">
    <svg width="40" height="44" viewBox="0 0 40 44"><path d="M6 40V22h8l6-14 4 2-2 12h12v8l-6 10z" stroke="#2b4d22" stroke-width="2" fill="none"/><circle cx="30" cy="8" r="4" stroke="#27235f" stroke-width="2" fill="none"/></svg>
    Quality Meets<br>Convenience</div>
  <div class="tab" style="left:822px">
    <svg width="42" height="42" viewBox="0 0 42 42"><path d="M4 4v34h34" stroke="#27235f" stroke-width="2" fill="none"/><rect x="10" y="24" width="5" height="12" fill="#2b4d22"/><rect x="19" y="18" width="5" height="18" fill="#2b4d22"/><rect x="28" y="12" width="5" height="24" fill="#2b4d22"/><path d="M8 22L22 10l6 4 10-10" stroke="#27235f" stroke-width="2" fill="none"/></svg>
    Pandemic-Proof &amp;<br>Recession-Ready</div>
  <h4 class="serif">Local Love</h4>
  <p class="copy">We celebrate the heart of Michigan by partnering with local legends. Say hello to Pine Ridge Jerky and Lakeshore Crisps—our hometown heroes. Their flavors dance on your taste buds, and we’re thrilled to bring them straight to your workplace.</p>
  <div class="why-photo" role="img" aria-label="Man browsing a row of illuminated vending machines"></div>
</section>

<section class="reviews">
  <h2 class="section-title serif">What Our <span class="t-green">Clients</span> <span class="t-navy">Say</span></h2>
  <span class="arrow prev"><svg width="16" height="16" viewBox="0 0 16 16"><path d="M14 8H3M7 3L2 8l5 5" stroke="#bbb" stroke-width="2" fill="none"/></svg></span>
  <div class="review" style="left:142px">
    <span class="quote">“</span><div class="stars">★★★★★</div>
    <p>Lorem ipsum dolor sit amet, consectetur adipiscing elit, sed do eiusmod tempor incididunt ut labore et dolore magna aliqua. Ut enim ad minim veniam, quis nostrud exercitation ullamco laboris nisi ut aliquip ex ea</p>
    <h5 class="serif">Rita Collins</h5>
  </div>
  <div class="review" style="left:614px">
    <span class="quote">“</span><div class="stars">★★★★★</div>
    <p>Lorem ipsum dolor sit amet, consectetur adipiscing elit, sed do eiusmod tempor incididunt ut labore et dolore magna aliqua. Ut enim ad minim veniam, quis nostrud exercitation ullamco laboris nisi ut aliquip ex ea</p>
    <h5 class="serif">Sam Porter</h5>
  </div>
  <span class="arrow next"><svg width="16" height="16" viewBox="0 0 16 16"><path d="M2 8h11M9 3l5 5-5 5" stroke="#fff" stroke-width="2" fill="none"/></svg></span>
</section>

<section class="cta">
  <h2 class="serif">Ready To Experience The <span class="t-green">Snack</span><span class="t-navy">Orbit</span><br>Difference?</h2>
  <p>Sign up now and let’s connect. Taste the future of snacking firsthand! Contact us today<br>and explore how our vending magic can elevate your space.</p>
  <span class="btn btn-green">Contact Us</span>
</section>

<footer class="footer">
  <svg class="wave" width="1200" height="365" viewBox="0 0 1200 365">
    <path d="M0 80 Q600 -40 1200 80 V365 H0z" fill="#27235f"/>
    <path d="M0 76 Q600 -48 1200 76" stroke="#27235f" stroke-width="4" fill="none" transform="translate(0,-8)"/>
  </svg>
  <div class="links foot-col">
    <h6>Quick Links</h6>
    <ul><li>Home</li><li>About Us</li><li>Why Choose SnackOrbit</li><li>Product and Services</li><li>Contact Us</li></ul>
  </div>
  <div class="foot-brand"><span class="brand-dot"></span>SnackOrbit</div>
  <div class="socials"><span></span><span></span><span></span><span></span></div>
  <div class="contact foot-col">
    <h6>Contact Details</h6>
    <div class="contact-row"><svg width="26" height="26" viewBox="0 0 26 26"><circle cx="13" cy="13" r="11" stroke="#fff" stroke-width="1.5" fill="none"/><path d="M2 13h22M13 2c-5 6-5 16 0 22M13 2c5 6 5 16 0 22" stroke="#fff" stroke-width="1.2" fill="none"/></svg><span>123, Building Name, Street<br>City, State XY 123456</span></div>
    <div class="contact-row"><svg width="26" height="26" viewBox="0 0 26 26"><path d="M5 3l5 1 2 6-3 2c2 4 4 6 8 8l2-3 6 2 1 5c-12 1-22-9-21-21z" stroke="#fff" stroke-width="1.5" fill="none"/></svg><span>PHONE<br>123-456-7890</span></div>
    <div class="contact-row"><svg width="26" height="26" viewBox="0 0 26 26"><rect x="2" y="6" width="22" height="16" stroke="#fff" stroke-width="1.5" fill="none"/><path d="M2 6l11 9 11-9" stroke="#fff" stroke-width="1.5" fill="none"/></svg><span>EMAIL<br>info@snackorbit.com</span></div>
  </div>
</footer>
<div class="copyright">© 2024 SnackOrbit. all rights reserved.</div>

</body>
</html>
```